Hvac and insulation company needs good looking business card design

We are hvac and insulation company and looking for a new business cards that look to today standards designs

Target Market(s)

homeowners

Industry/Entity Type

Hvac

Contact Information for Business Card

Name: Walter Brinoku
Home comfort consultant
address: 4827 Dunmore St #215 Oakland, CA 94619
office: 888-316-2790
cell: 510-742-3185
Lic.# 584261
Email: walter@corvane-hvac.com
Web: corvane-hvac.com

Requirements
Must have
• clean and sleek look
Nice to have
• simple with a clean look
Should not have
• to busy business card

```html
<!DOCTYPE html>
<html lang="en">
<head>
<meta charset="utf-8">
<title>Corvane business cards</title>
<link rel="stylesheet" href="https://fonts.googleapis.com/css2?family=Poppins:wght@400;600;700&family=Roboto:wght@400;500&display=swap">
<style>
  :root {
    --stage: #2a2a2a;
    --card-black: #141414;
    --orange: #f7931e;
    --orange-deep: #f07d0e;
    --white: #ffffff;
    --paper-grey: #ececec;
    --title-grey: #777777;
    --web-grey: #d9d9d9;
  }
  * { margin: 0; padding: 0; box-sizing: border-box; }
  html, body { width: 1200px; height: 886px; overflow: hidden; background: var(--stage); }
  .stage { position: relative; width: 1200px; height: 886px; }

  .card {
    position: absolute; width: 520px; height: 300px;
    border-radius: 16px; overflow: hidden;
    box-shadow: 0 14px 30px rgba(0,0,0,.45);
  }

  /* back */
  .card-back { left: 80px; top: 90px; background: var(--card-black); }
  .back-brand {
    position: absolute; left: 0; right: 0; top: 110px;
    display: flex; align-items: center; justify-content: center; gap: 14px;
  }
  .brand-mark { width: 34px; height: 34px; background: var(--orange); border-radius: 4px; }
  .brand-name {
    font-family: "Poppins", sans-serif; font-weight: 700; font-size: 56px;
    line-height: 1; color: var(--orange); letter-spacing: -1px;
  }
  .back-web {
    position: absolute; left: 0; right: 0; bottom: 46px; text-align: center;
    font-family: "Poppins", sans-serif; font-size: 13px; letter-spacing: 7px;
    color: var(--web-grey);
  }

  /* front */
  .card-front { left: 600px; top: 480px; background: var(--paper-grey); }
  .front-art { position: absolute; inset: 0; }
  .front-brand {
    position: absolute; left: 34px; top: 42px;
    display: flex; align-items: center; gap: 10px;
  }
  .front-brand .brand-mark { width: 26px; height: 26px; background: var(--white); }
  .front-brand .brand-name { color: var(--white); font-size: 40px; }

  .contact {
    position: absolute; left: 34px; top: 138px;
    font-family: "Roboto", sans-serif; color: var(--white); font-size: 12.5px; line-height: 1.35;
  }
  .contact-address { margin-bottom: 8px; width: 190px; }
  .contact-list { list-style: none; }
  .contact-list li { display: flex; align-items: center; gap: 8px; height: 17px; }
  .contact-list svg { width: 11px; height: 11px; flex: none; }

  .person {
    position: absolute; left: 300px; top: 92px; width: 150px; text-align: center;
    font-family: "Roboto", sans-serif; font-weight: 500;
  }
  .person-name { color: var(--orange); font-size: 19px; text-transform: uppercase; }
  .person-title { color: var(--title-grey); font-size: 11px; text-transform: uppercase; margin-top: 4px; letter-spacing: .3px; }
</style>
</head>
<body>
<main class="stage">

  <section class="card card-back" aria-label="Card back">
    <div class="back-brand">
      <span class="brand-mark"></span>
      <span class="brand-name">corvane</span>
    </div>
    <p class="back-web">www.corvane-hvac.com</p>
  </section>

  <section class="card card-front" aria-label="Card front">
    <svg class="front-art" viewBox="0 0 520 300" width="520" height="300" aria-hidden="true">
      <defs>
        <linearGradient id="orangeField" x1="0" y1="0" x2="1" y2="1">
          <stop offset="0" stop-color="#f7931e"/>
          <stop offset="0.6" stop-color="#f69c34"/>
          <stop offset="1" stop-color="#f07d0e"/>
        </linearGradient>
      </defs>
      <polygon points="0,0 300,0 280,175 420,300 0,300" fill="url(#orangeField)"/>
      <polygon points="330,20 478,62 440,214 292,172" fill="none" stroke="#f7931e" stroke-width="3"/>
      <polygon points="320,14 468,56 430,208 282,166" fill="#ffffff"/>
    </svg>

    <div class="front-brand">
      <span class="brand-mark"></span>
      <span class="brand-name">corvane</span>
    </div>

    <div class="contact">
      <p class="contact-address">4827 Dunmore St #215<br>Oakland, CA 94619</p>
      <ul class="contact-list">
        <li><svg viewBox="0 0 12 12"><path d="M2.5 1h2l1 3-1.3 1a6 6 0 0 0 2.8 2.8l1-1.3 3 1v2c0 .8-.7 1.5-1.5 1.5A9 9 0 0 1 1 2.5C1 1.7 1.7 1 2.5 1z" fill="#fff"/></svg>888-316-2790</li>
        <li><svg viewBox="0 0 12 12"><rect x="3" y="0.5" width="6" height="11" rx="1" fill="none" stroke="#fff" stroke-width="1.2"/><circle cx="6" cy="9.5" r=".7" fill="#fff"/></svg>510-742-3185</li>
        <li><svg viewBox="0 0 12 12"><rect x="1" y="1" width="10" height="10" rx="1.5" fill="none" stroke="#fff" stroke-width="1.2"/><path d="M3.5 4.5h5M3.5 7.5h3" stroke="#fff" stroke-width="1.2"/></svg>Lic.# 584261</li>
        <li><svg viewBox="0 0 12 12"><rect x="0.5" y="2" width="11" height="8" rx="1" fill="#fff"/><path d="M1 2.5l5 4 5-4" fill="none" stroke="#f7931e" stroke-width="1.1"/></svg>walter@corvane-hvac.com</li>
        <li><svg viewBox="0 0 12 12"><circle cx="6" cy="6" r="5" fill="none" stroke="#fff" stroke-width="1.2"/><path d="M1 6h10M6 1c-2.5 3-2.5 7 0 10M6 1c2.5 3 2.5 7 0 10" fill="none" stroke="#fff" stroke-width="1"/></svg>corvane-hvac.com</li>
      </ul>
    </div>

    <div class="person">
      <p class="person-name">Walter Brinoku</p>
      <p class="person-title">Home Comfort Consultant</p>
    </div>
  </section>

</main>
</body>
</html>
```